Elevating our current Business Card Design

We want to elevate our current business card with a new design to look like a zenith 300 company. We are a premium lubricant distributor (oil and grease).
We need 2 versions, version 1 is as per the uploaded a copy of our current business card with the English version.
For our Chinese version we need to use the front to be English in English and have the back of the card designed exactly like the front for all info to be in Chinese.
The design template needs to be such that we can amend the template with adding different information for each person's card.
The background colour of the card can be changed- we just need to clearly see all information on the card and logos.
The QJR and Ember steady logos cannot have any colour or display changes- only use the logos attached.
All logos need to be included and all information from the attached current card

```html
<!DOCTYPE html>
<html lang="en">
<head>
<meta charset="utf-8">
<title>Corvale Lubricants – Business Card</title>
<link href="https://fonts.googleapis.com/css2?family=Open+Sans:wght@400;600;700&family=Ubuntu:wght@700&display=swap" rel="stylesheet">
<style>
  :root{
    --stage:#232323;
    --gold:#d29e2a;
    --gold-light:#e9c040;
    --red:#e52a24;
    --red-deep:#9b1a1f;
    --orange:#f07a1a;
    --green:#06301f;
    --white:#ffffff;
    --grey:#9a9a9a;
    --ink:#1e1e1e;
  }
  *{box-sizing:border-box;margin:0;padding:0}
  html,body{width:1200px;height:780px;overflow:hidden;background:var(--stage)}
  body{position:relative;font-family:"Open Sans",Arial,sans-serif}

  .card{position:absolute;width:580px;height:331px;border-radius:22px;overflow:hidden;box-shadow:0 14px 30px rgba(0,0,0,.55)}

  /* Back of card */
  .card--back{left:60px;top:50px}
  .card-back__pattern{position:absolute;inset:0;background:radial-gradient(circle at 50% 50%,var(--gold-light) 0%,var(--gold) 70%)}
  .card-back__brand{position:absolute;left:0;right:0;top:50%;transform:translateY(-50%);display:flex;align-items:center;justify-content:center;gap:16px}
  .card-back__brand .brand-dot{width:46px;height:46px;border-radius:50%;background:var(--white)}
  .card-back__brand .brand-name{font-weight:700;font-size:50px;letter-spacing:2px;color:var(--white)}

  /* Front of card */
  .card--front{left:560px;top:400px;background:var(--white)}
  .card-front__waves{position:absolute;inset:0}
  .card-front__brand{position:absolute;right:30px;top:26px;display:flex;align-items:center;gap:12px}
  .card-front__brand .brand-dot{width:34px;height:34px;border-radius:50%;background:var(--gold)}
  .card-front__brand .brand-name{font-weight:700;font-size:34px;letter-spacing:1.5px;color:var(--red)}

  .person{position:absolute;left:30px;top:76px}
  .person__name{font-family:"Ubuntu",Arial,sans-serif;font-weight:700;font-size:27px;color:var(--red);line-height:1}
  .person__role{font-size:12.5px;font-weight:600;color:var(--ink);margin-top:4px}

  .contact{position:absolute;left:34px;top:194px;color:var(--white);font-size:12px;line-height:16px}
  .contact__address{margin-bottom:6px}
  .contact__list{list-style:none}
  .contact__list li{display:flex;align-items:center;gap:8px;height:16px;white-space:nowrap}
  .contact__list svg{width:11px;height:11px;flex:none}

  .credentials{position:absolute;right:18px;bottom:22px;width:250px}
  .credentials__badges{display:flex;align-items:flex-end;justify-content:flex-end;gap:12px;margin-bottom:8px}
  .badge-ember{width:52px;height:30px;border:4px solid var(--white);border-bottom:none;border-radius:30px 30px 0 0}
  .badge-cert{width:34px;height:34px;border-radius:50%;border:4px solid var(--grey);display:flex;align-items:center;justify-content:center}
  .badge-cert span{width:18px;height:18px;border-radius:50%;background:var(--orange)}
  .credentials__strip{display:flex;height:36px;border:2px solid var(--red)}
  .strip-distributor{flex:1.6;background:var(--white);display:flex;align-items:center;gap:6px;padding-left:8px;white-space:nowrap}
  .strip-distributor .brand-dot{width:12px;height:12px;border-radius:50%;background:var(--gold);flex:none}
  .strip-distributor .brand-name{font-weight:700;font-size:12px;color:var(--red)}
  .strip-partner{flex:1;background:var(--red)}
</style>
</head>
<body>

<section class="card card--back" aria-label="Card back">
  <div class="card-back__pattern" role="img" aria-label="Gold foil background with repeated brand pattern"></div>
  <div class="card-back__brand">
    <span class="brand-dot"></span>
    <span class="brand-name">CORVALE</span>
  </div>
</section>

<section class="card card--front" aria-label="Card front">
  <svg class="card-front__waves" viewBox="0 0 580 331" preserveAspectRatio="none" aria-hidden="true">
    <path d="M0 182 C140 140 320 132 420 130 C500 128 555 95 580 40 L580 331 L0 331 Z" fill="var(--green)"/>
    <path d="M0 175 C140 133 320 125 420 123 C500 121 552 88 578 34" fill="none" stroke="var(--red-deep)" stroke-width="7"/>
    <path d="M0 164 C120 128 240 118 330 116" fill="none" stroke="var(--orange)" stroke-width="4"/>
    <path d="M20 172 C140 134 260 124 350 120" fill="none" stroke="var(--red)" stroke-width="2"/>
    <path d="M440 114 C510 108 552 78 572 28" fill="none" stroke="var(--gold)" stroke-width="4"/>
  </svg>

  <div class="card-front__brand">
    <span class="brand-dot"></span>
    <span class="brand-name">CORVALE</span>
  </div>

  <div class="person">
    <h1 class="person__name">Maren Kolbe</h1>
    <p class="person__role">Administration Executive</p>
  </div>

  <div class="contact">
    <p class="contact__address">48 Depot Crescent<br>Harlow Park, WA 6190</p>
    <ul class="contact__list">
      <li><svg viewBox="0 0 12 12"><path d="M2 1h3l1 3-2 1a7 7 0 0 0 3 3l1-2 3 1v3c-6 0-10-4-9-9z" fill="var(--red)"/></svg>1300 000 412</li>
      <li><svg viewBox="0 0 12 12"><rect x="3" y="0.5" width="6" height="11" rx="1" fill="none" stroke="var(--red)" stroke-width="1.2"/></svg>+61 400 123 456</li>
      <li><svg viewBox="0 0 12 12"><rect x="1" y="5" width="10" height="6" fill="var(--red)"/><rect x="3" y="1" width="6" height="4" fill="none" stroke="var(--red)"/></svg>+61 8 9000 1234</li>
      <li><svg viewBox="0 0 12 12"><circle cx="6" cy="6" r="5" fill="none" stroke="var(--red)" stroke-width="1.4"/><path d="M1 6h10M6 1c-3 3-3 7 0 10M6 1c3 3 3 7 0 10" fill="none" stroke="var(--red)"/></svg>www.corvaledirect.com</li>
      <li><svg viewBox="0 0 12 12"><rect x="0.5" y="2" width="11" height="8" fill="var(--red)"/><path d="M1 2.5l5 4 5-4" fill="none" stroke="var(--white)"/></svg>maren.kolbe@corvaledirect.com</li>
    </ul>
  </div>

  <div class="credentials">
    <div class="credentials__badges">
      <div class="badge-ember" role="img" aria-label="Ember steady network member badge"></div>
      <div class="badge-cert" role="img" aria-label="QJR certification badge"><span></span></div>
      <div class="badge-cert" role="img" aria-label="QJR certification badge"><span></span></div>
      <div class="badge-cert" role="img" aria-label="QJR certification badge"><span></span></div>
    </div>
    <div class="credentials__strip">
      <div class="strip-distributor"><span class="brand-dot"></span><span class="brand-name">Corvale Lubricants</span></div>
      <div class="strip-partner" role="img" aria-label="Tessaro partner badge"></div>
    </div>
  </div>
</section>

</body>
</html>
```